WTF!!! We need a modern professional website for a business litigation law firm.

We need a modern, clean, professional and uncomplicated website for a new business trial and litigation law firm called "Haverlock Trial Firm PLLC". Website must be mobile optimized for iPad and smartphone. The law firm specializes in counseling and representing large corporations, small businesses and entrepreneurs in and out of the courtroom. Lawyers in the firm serve as Florida counsel and trial counsel to organizations facing claims involving product liability, premises liability, professional liability, vehicle and transportation liability, warranty claims, construction defects and delay claims, complex business disputes, commercial litigation and bid disputes in State and Federal Courts. The website is mainly to provide information about the firm, and should include sections describing the firm, identifying the Industries Served and Areas of Practice ," a separate page identifying the "Professionals", a separate page for "Resources & Advisories," and a traveling "Connect With Us" button a site visitor can click on that will launch an email to the Firm's general email account. The website should allow us to easily modify the content on these pages, and let us add/modify links to external information sources. We will not sell anything or take payments through the website. We do need to be able to easily upload and update photographs of attorneys and add new attorneys names/email hyperlinks as the firm grows. We would like to add developments in the law or success stories easily and quickly, such as through a blog page. On the "Connect With Us" page the website should have hyperlinks to email the Firm, and there should be hyperlinks to email each professional on the "Professionals" page. The website should be viewable on mobile devices without distortion. The law firm focuses on trial work and should have some imagery associated with courtrooms, but the overall theme of the site should be modern, clean, and communicate sophistication and strength. The website should be made in Wordpress. We have uploaded logo files for Haverlock Trial Firm.

Target Market(s)

Corporations and companies that are looking for legal representation. Other attorneys/legal industry.

Industry/Entity Type

Legal Industry

Coding

Coded - Design and coding required

Number of Pages Required

1 page

Font styles to use
Sans Serif

Requirements
Must have
• Simple, clean, sophisticated, modern website that includes the logo, watermark of logo, and the elements described above.
Nice to have
• Pictures of city scape, buildings, courtroom, team members.

```html
<!DOCTYPE html>
<html lang="en">
<head>
<meta charset="utf-8">
<title>Haverlock Trial Firm PLLC</title>
<link href="https://fonts.googleapis.com/css2?family=Heebo:wght@400;500;700;800&family=Roboto:ital,wght@0,400;0,500;0,700;1,400&display=swap" rel="stylesheet">
<style>
:root{
  --gold:#b8813e;
  --navy:#1b2a3e;
  --ink:#1a2433;
  --dark:#141414;
  --card-line:#3a3a3a;
  --text:#5a5f66;
  --light:#eef0f3;
  --white:#ffffff;
}
*{margin:0;padding:0;box-sizing:border-box}
html,body{width:1200px;height:5106px;overflow:hidden}
body{position:relative;background:var(--white);font-family:"Roboto",Arial,sans-serif;color:var(--text)}
.abs{position:absolute}
.head{font-family:"Heebo",Arial,sans-serif;font-weight:800;color:var(--ink);letter-spacing:-.5px;text-transform:uppercase}
.mark{width:14px;height:14px;background:var(--ink)}
.mark.light{background:var(--white)}
.photo{position:absolute}
.btn{position:absolute;display:flex;align-items:stretch;font-family:"Heebo",sans-serif;font-weight:700;font-size:13px;text-transform:uppercase;text-decoration:none}
.btn .lbl{display:flex;align-items:center;padding:0 18px;background:var(--ink);color:var(--white)}
.btn .go{width:42px;background:var(--gold);display:flex;align-items:center;justify-content:center}
.arrow-circle{position:absolute;width:40px;height:40px;border-radius:50%;display:flex;align-items:center;justify-content:center}
.arrow-circle.outline{border:1.5px solid #333;background:#fff}
.arrow-circle.filled{background:var(--gold)}

/* hero */
.hero{position:absolute;left:0;top:0;width:1200px;height:626px;clip-path:polygon(0 0,100% 0,100% 520px,0 626px);
  background:
    radial-gradient(ellipse 700px 160px at 50% 470px,rgba(255,170,80,.75),rgba(255,170,80,0) 70%),
    radial-gradient(ellipse 380px 260px at 1080px 60px,rgba(60,90,230,.6),rgba(60,90,230,0) 70%),
    linear-gradient(180deg,#1f3fb4 0%,#3253c6 18%,#5a64b4 34%,#9a6c8e 46%,#d98458 56%,#c9764a 63%,#4d5066 74%,#2c3446 86%,#1d222c 100%)}
.hero-dots{position:absolute;top:534px;left:566px;display:flex;gap:8px}
.hero-dots i{width:8px;height:8px;border-radius:50%;background:rgba(255,255,255,.55)}
.hero-dots i.on{background:#fff}
.brand{position:absolute;left:110px;top:62px;color:var(--white);font-family:"Heebo",sans-serif;font-weight:700;font-size:24px;line-height:26px;text-transform:uppercase}
.topinfo{position:absolute;display:flex;align-items:center;gap:14px;color:var(--white);font-size:14px;line-height:20px}
.topinfo b{font-weight:700;font-size:13px}
.ic-gold{width:40px;height:40px;border-radius:50%;background:var(--gold);display:flex;align-items:center;justify-content:center;flex:none}
.nav{position:absolute;top:90px;left:320px;font-family:"Heebo",sans-serif;font-weight:700;font-size:14px;color:var(--white)}
.nav a{color:var(--white);text-decoration:none;position:absolute;white-space:nowrap}
.nav a.active{color:var(--gold)}
.nav a.active::before{content:"";position:absolute;left:0;top:-12px;width:44px;height:3px;background:var(--white)}
.welcome{position:absolute;left:0;width:1200px;text-align:center;color:var(--white);font-family:"Heebo",sans-serif;text-shadow:0 2px 10px rgba(0,0,0,.25)}

/* industries */
.ind-card{position:absolute;top:807px;width:236px;height:302px}
.ind-label{position:absolute;left:20px;top:275px;width:196px;height:54px;background:#fff;box-shadow:0 4px 14px rgba(0,0,0,.12);display:flex;align-items:center;justify-content:center;font-family:"Heebo",sans-serif;font-weight:700;font-size:15px;color:var(--ink)}
.ind-label.on{background:var(--gold);color:#fff}

/* practice */
.pa-card{position:absolute;width:308px;height:298px;border:1.5px solid var(--card-line);text-align:center;padding:0 18px}
.pa-card.on{border-color:var(--gold);background:#1f1a14}
.pa-icon{width:74px;height:74px;border-radius:50%;background:#262626;margin:34px auto 0;display:flex;align-items:center;justify-content:center}
.pa-card.on .pa-icon{background:#3a2c1a;border:2px solid var(--gold)}
.pa-title{margin-top:22px;font-family:"Heebo",sans-serif;font-weight:700;font-size:15px;color:#fff;text-transform:uppercase}
.pa-card.on .pa-title{color:var(--gold)}
.pa-text{margin-top:12px;font-size:15px;line-height:26px;color:#8a8a8a}
.pa-card.on .pa-text{color:#fff}
.pa-go{margin-top:6px}

/* professionals */
.pro-card{position:absolute;top:2978px;width:236px;height:302px}
.pro-label{position:absolute;left:20px;top:272px;width:196px;height:54px;background:#fff;box-shadow:0 4px 14px rgba(0,0,0,.12);display:flex;align-items:center;justify-content:center;font-family:"Heebo",sans-serif;font-weight:700;font-size:15px;color:var(--ink);text-transform:uppercase}
.pro-label.on{left:6px;top:248px;width:224px;height:80px;background:var(--gold);color:#fff;flex-direction:column;font-size:18px}
.pro-label.on small{font-family:"Roboto",sans-serif;font-style:italic;font-weight:400;font-size:10px;margin-top:4px}

/* testimonials */
.testi-bg{position:absolute;left:0;top:3444px;width:1200px;height:556px;background:var(--light);clip-path:polygon(0 0,100% 0,100% 471px,0 556px)}
.av{position:absolute;border-radius:50%;border:3px solid #fff;box-shadow:0 2px 8px rgba(0,0,0,.15)}

/* blog */
.blog-card{position:absolute;top:4192px;width:300px;height:390px;background:#fff;box-shadow:0 2px 12px rgba(0,0,0,.12)}
.blog-card h3{position:absolute;left:14px;top:218px;font-family:"Heebo",sans-serif;font-weight:700;font-size:15px;color:var(--ink);text-transform:uppercase}
.blog-card p{position:absolute;left:14px;top:246px;width:276px;font-size:15px;line-height:26px;color:#555}
.blog-card .go{position:absolute;right:16px;bottom:14px}

/* footer */
.footer{position:absolute;left:0;top:4650px;width:1200px;height:456px;background:var(--navy);clip-path:polygon(0 85px,100% 0,100% 100%,0 100%)}
.f-head{position:absolute;font-family:"Heebo",sans-serif;font-weight:700;font-size:19px;color:#fff;text-transform:uppercase}
.f-links{position:absolute;left:392px;top:4830px;list-style:none;font-family:"Heebo",sans-serif;font-weight:500;font-size:14px;color:#fff;line-height:30px;text-transform:uppercase}
.f-item{position:absolute;display:flex;gap:14px;color:#fff;font-size:15px;line-height:20px}
.f-item b{font-family:"Heebo",sans-serif;font-weight:700;font-size:14px}
.social{position:absolute;width:50px;height:50px;border-radius:50%;border:1.5px solid #fff}
.social.on{background:var(--gold);border-color:var(--gold)}
</style>
</head>
<body>

<!-- HERO -->
<section class="hero" role="img" aria-label="Downtown city skyline with glass towers glowing at sunset"></section>
<div class="hero-dots"><i></i><i class="on"></i><i></i></div>
<div class="brand">Haverlock<br>Trial Firm</div>
<div class="topinfo" style="left:384px;top:20px">
  <div class="ic-gold"><svg width="18" height="18" viewBox="0 0 24 24"><path fill="#fff" d="M6.6 10.8a15 15 0 0 0 6.6 6.6l2.2-2.2c.3-.3.7-.4 1-.2 1.1.4 2.3.6 3.6.6.6 0 1 .4 1 1V20c0 .6-.4 1-1 1A17 17 0 0 1 3 4c0-.6.4-1 1-1h3.5c.6 0 1 .4 1 1 0 1.3.2 2.5.6 3.6.1.3 0 .7-.2 1z"/></svg></div>
  <div><b>PHONE NO:</b><br>+1(888) 888 8888</div>
</div>
<div class="topinfo" style="left:642px;top:20px">
  <div class="ic-gold"><svg width="18" height="18" viewBox="0 0 24 24"><path fill="#fff" d="M3 5h18v14H3z"/><path fill="none" stroke="#b8813e" stroke-width="2" d="M3 6l9 7 9-7"/></svg></div>
  <div><b>EMAIL:</b><br>haverlocktrialfirm.com</div>
</div>
<a class="btn" style="left:928px;top:18px;height:44px">
  <span class="lbl" style="background:#111a2a">CONTACT US</span>
  <span class="go"><svg width="10" height="14" viewBox="0 0 10 14"><path d="M2 1l6 6-6 6" stroke="#fff" stroke-width="2" fill="none"/></svg></span>
</a>
<nav class="nav">
  <a class="active" style="left:0">HOME</a>
  <a style="left:78px">ABOUT US</a>
  <a style="left:187px">PRACTICE AREA</a>
  <a style="left:340px">PROFESSIONALS</a>
  <a style="left:503px">RESOURCES &amp; ADVISORIES</a>
  <a style="left:740px">BLOG</a>
</nav>
<div class="welcome" style="top:162px;font-size:34px;font-weight:500;letter-spacing:1px">WELCOME TO</div>
<h1 class="welcome" style="top:212px;font-size:66px;font-weight:800;letter-spacing:-1px">HAVERLOCK TRIAL FIRM PLLC</h1>
<a class="btn" style="left:496px;top:310px;height:44px">
  <span class="lbl" style="background:#111a2a">CONNECT WITH US</span>
  <span class="go"><svg width="10" height="14" viewBox="0 0 10 14"><path d="M2 1l6 6-6 6" stroke="#fff" stroke-width="2" fill="none"/></svg></span>
</a>

<!-- INDUSTRIES -->
<h2 class="head abs" style="left:112px;top:676px;font-size:39px">Our Industries Served</h2>
<div class="mark abs" style="left:112px;top:742px"></div>
<p class="abs" style="left:640px;top:678px;width:440px;font-size:15.5px;line-height:26px">Lorem ipsum dolor sit amet, consectetur adipiscing elit, sed do eiusmod tempor incididunt ut labore et dolore magna aliqua Quis ipsum suspendisse.</p>
<div class="arrow-circle outline" style="left:48px;top:939px"><svg width="10" height="14" viewBox="0 0 10 14"><path d="M8 1L2 7l6 6" stroke="#222" stroke-width="2" fill="none"/></svg></div>
<div class="arrow-circle filled" style="left:1110px;top:939px"><svg width="10" height="14" viewBox="0 0 10 14"><path d="M2 1l6 6-6 6" stroke="#fff" stroke-width="2" fill="none"/></svg></div>
<div class="ind-card" style="left:112px"><div class="photo" role="img" aria-label="Attorney in a dark suit at a meeting table" style="inset:0;background:radial-gradient(ellipse 120px 150px at 130px 110px,#6b5440,rgba(107,84,64,0) 70%),linear-gradient(170deg,#2e2822 0%,#1c1814 55%,#3a3026 100%)"></div><div class="ind-label">CRIMINAL DEFENSE</div></div>
<div class="ind-card" style="left:358px"><div class="photo" role="img" aria-label="Doctor in a white coat consulting with a colleague" style="inset:0;background:radial-gradient(ellipse 110px 170px at 150px 200px,#f1efec,rgba(241,239,236,0) 70%),linear-gradient(160deg,#9a8470 0%,#c8b8a6 45%,#6a584a 100%)"></div><div class="ind-label on">HEALTHCARE</div></div>
<div class="ind-card" style="left:606px"><div class="photo" role="img" aria-label="Professionals reviewing property documents at a desk" style="inset:0;background:radial-gradient(ellipse 140px 120px at 90px 90px,#e6e3de,rgba(230,227,222,0) 70%),linear-gradient(160deg,#c9c4bc 0%,#8a847c 50%,#3e3a36 100%)"></div><div class="ind-label">REAL ESTATE</div></div>
<div class="ind-card" style="left:852px"><div class="photo" role="img" aria-label="Man standing inside a wood-panelled courtroom" style="inset:0;background:radial-gradient(ellipse 90px 70px at 118px 40px,#d7c6ae,rgba(215,198,174,0) 70%),linear-gradient(180deg,#8a5e3c 0%,#6a4228 45%,#3a2416 80%,#2a1a10 100%)"></div><div class="ind-label">CONSTRUCTION</div></div>

<!-- ABOUT -->
<div class="abs" style="left:0;top:1287px;width:1200px;height:520px;background:var(--light)"></div>
<div class="abs" style="left:954px;top:1287px;width:246px;height:393px;background:linear-gradient(160deg,#2c3e58,#1f2d42)"></div>
<div class="abs" style="left:678px;top:1500px;width:307px;height:155px;border:6px solid var(--gold)"></div>
<div class="photo" role="img" aria-label="Smiling senior attorney in a dark suit in a bright office" style="left:700px;top:1336px;width:310px;height:294px;background:radial-gradient(ellipse 140px 130px at 200px 300px,#1e2228,rgba(30,34,40,0) 80%),linear-gradient(110deg,#7e9ab4 0%,#b7c9d8 35%,#e3e8ec 60%,#8a96a2 100%)"></div>
<h2 class="head abs" style="left:112px;top:1343px;font-size:39px;line-height:46px">About Haverlock<br>Trial Firm</h2>
<div class="mark abs" style="left:112px;top:1452px"></div>
<p class="abs" style="left:112px;top:1502px;width:490px;font-size:15px;line-height:26.5px">Lorem ipsum dolor sit amet, consectetur adipiscing elit, sed do sod tempor incididunt ut labore et dolore magna aliqua. Quis ipsum isse ultrices gravida. Risus commodo viverra maeeas acumsan lacus m ipsum dolor sit amet, consectetur adipiscing elit, sed do eiumod mpor incididunt ut labore et dolore magna aliqua.</p>
<a class="btn" style="left:112px;top:1655px;height:46px">
  <span class="lbl">READ MORE</span>
  <span class="go"><svg width="10" height="14" viewBox="0 0 10 14"><path d="M2 1l6 6-6 6" stroke="#fff" stroke-width="2" fill="none"/></svg></span>
</a>

<!-- PRACTICE AREAS -->
<div class="abs" style="left:0;top:1718px;width:1200px;height:1072px;background:var(--dark);clip-path:polygon(0 72px,100% 0,100% 962px,0 1072px)"></div>
<h2 class="head abs" style="left:0;top:1818px;width:1200px;text-align:center;font-size:39px;color:#fff">Our Practice Areas</h2>
<div class="mark light abs" style="left:593px;top:1882px"></div>

<div class="pa-card" style="left:112px;top:1963px"><div class="pa-icon"><svg width="34" height="34" viewBox="0 0 34 34" fill="none" stroke="#fff" stroke-width="2"><rect x="8" y="4" width="18" height="24"/><path d="M12 11h10M12 16h10M12 21h6"/></svg></div><div class="pa-title">Product Liability</div><p class="pa-text">Lorem ipsum dolor sit amet, coneeur adipiscing elit, sed do sod tempor incididunt ut</p><div class="pa-go"><svg width="14" height="12" viewBox="0 0 14 12"><path d="M0 6h11M7 1l5 5-5 5" stroke="#b8813e" stroke-width="2.2" fill="none"/></svg></div></div>
<div class="pa-card on" style="left:446px;top:1963px"><div class="pa-icon"><svg width="34" height="34" viewBox="0 0 34 34" fill="none" stroke="#b8813e" stroke-width="2"><rect x="8" y="6" width="18" height="22"/><path d="M12 11h3M19 11h3M12 16h3M19 16h3M12 21h3M19 21h3"/></svg></div><div class="pa-title">Premises Liability</div><p class="pa-text">Lorem ipsum dolor sit amet, coneeur adipiscing elit, sed do sod tempor incididunt ut</p><div class="pa-go"><svg width="14" height="12" viewBox="0 0 14 12"><path d="M0 6h11M7 1l5 5-5 5" stroke="#b8813e" stroke-width="2.2" fill="none"/></svg></div></div>
<div class="pa-card" style="left:780px;top:1963px"><div class="pa-icon"><svg width="34" height="34" viewBox="0 0 34 34" fill="none" stroke="#fff" stroke-width="2"><circle cx="15" cy="11" r="5"/><path d="M6 28c0-6 4-9 9-9s9 3 9 9"/><path d="M22 24l3 3 5-6"/></svg></div><div class="pa-title">Professional Liability</div><p class="pa-text">Lorem ipsum dolor sit amet, coneeur adipiscing elit, sed do sod tempor incididunt ut</p><div class="pa-go"><svg width="14" height="12" viewBox="0 0 14 12"><path d="M0 6h11M7 1l5 5-5 5" stroke="#b8813e" stroke-width="2.2" fill="none"/></svg></div></div>

<div class="pa-card" style="left:112px;top:2292px"><div class="pa-icon"><svg width="36" height="34" viewBox="0 0 36 34" fill="none" stroke="#fff" stroke-width="2"><rect x="3" y="10" width="20" height="13"/><path d="M23 14h6l4 5v4H23"/><circle cx="10" cy="25" r="3"/><circle cx="27" cy="25" r="3"/></svg></div><div class="pa-title">Transportation Liability</div><p class="pa-text">Lorem ipsum dolor sit amet, coneeur adipiscing elit, sed do sod tempor incididunt ut</p><div class="pa-go"><svg width="14" height="12" viewBox="0 0 14 12"><path d="M0 6h11M7 1l5 5-5 5" stroke="#b8813e" stroke-width="2.2" fill="none"/></svg></div></div>
<div class="pa-card" style="left:446px;top:2292px"><div class="pa-icon"><svg width="34" height="34" viewBox="0 0 34 34" fill="none" stroke="#fff" stroke-width="2"><circle cx="17" cy="17" r="12"/><circle cx="17" cy="17" r="6"/><path d="M17 13l1.2 2.6 2.8.3-2 2 .6 2.8-2.6-1.4-2.6 1.4.6-2.8-2-2 2.8-.3z" fill="#fff" stroke="none"/></svg></div><div class="pa-title">Warranty Claims</div><p class="pa-text">Lorem ipsum dolor sit amet, coneeur adipiscing elit, sed do sod tempor incididunt ut</p><div class="pa-go"><svg width="14" height="12" viewBox="0 0 14 12"><path d="M0 6h11M7 1l5 5-5 5" stroke="#b8813e" stroke-width="2.2" fill="none"/></svg></div></div>
<div class="pa-card" style="left:780px;top:2292px"><div class="pa-icon"><svg width="36" height="34" viewBox="0 0 36 34" fill="none" stroke="#fff" stroke-width="2"><circle cx="18" cy="8" r="4"/><path d="M4 20l8-4 6 4 6-4 8 4M10 22l6 5M14 20l6 5M20 18l5 4"/></svg></div><div class="pa-title">Complex Business Disputes</div><p class="pa-text">Lorem ipsum dolor sit amet, coneeur adipiscing elit, sed do sod tempor incididunt ut</p><div class="pa-go"><svg width="14" height="12" viewBox="0 0 14 12"><path d="M0 6h11M7 1l5 5-5 5" stroke="#b8813e" stroke-width="2.2" fill="none"/></svg></div></div>

<a class="btn" style="left:516px;top:2630px;height:46px">
  <span class="lbl" style="background:#fff;color:var(--ink)">VIEW MORE</span>
  <span class="go"><svg width="10" height="14" viewBox="0 0 10 14"><path d="M2 1l6 6-6 6" stroke="#fff" stroke-width="2" fill="none"/></svg></span>
</a>

<!-- PROFESSIONALS -->
<h2 class="head abs" style="left:0;top:2838px;width:1200px;text-align:center;font-size:39px">Our Professionals</h2>
<div class="mark abs" style="left:593px;top:2902px"></div>
<div class="arrow-circle outline" style="left:50px;top:3122px"><svg width="10" height="14" viewBox="0 0 10 14"><path d="M8 1L2 7l6 6" stroke="#222" stroke-width="2" fill="none"/></svg></div>
<div class="arrow-circle filled" style="left:1112px;top:3122px"><svg width="10" height="14" viewBox="0 0 10 14"><path d="M2 1l6 6-6 6" stroke="#fff" stroke-width="2" fill="none"/></svg></div>
<div class="pro-card" style="left:112px"><div class="photo" role="img" aria-label="Portrait of an attorney in a navy suit" style="inset:0;background:radial-gradient(ellipse 80px 90px at 118px 110px,#c9a48a,rgba(201,164,138,0) 75%),linear-gradient(180deg,#8e9aa6 0%,#6c7886 45%,#2a3a52 75%,#1c2a40 100%)"></div><div class="pro-label">Daniel Whitmore</div></div>
<div class="pro-card" style="left:358px"><div class="photo" role="img" aria-label="Portrait of a business lawyer in a dark blazer" style="inset:0;background:radial-gradient(ellipse 80px 90px at 118px 110px,#d2aa90,rgba(210,170,144,0) 75%),linear-gradient(180deg,#a89a8c 0%,#6e5a4c 45%,#2a221e 75%,#1c1614 100%)"></div><div class="pro-label on">Claire Benton<small>BUSINESS LAWYER</small></div></div>
<div class="pro-card" style="left:606px"><div class="photo" role="img" aria-label="Portrait of an attorney in a grey suit" style="inset:0;background:radial-gradient(ellipse 80px 90px at 118px 110px,#c7987a,rgba(199,152,122,0) 75%),linear-gradient(180deg,#4c5a6c 0%,#3a4658 45%,#565e68 75%,#2a3240 100%)"></div><div class="pro-label">Owen Marshall</div></div>
<div class="pro-card" style="left:852px"><div class="photo" role="img" aria-label="Portrait of a smiling attorney in a light suit" style="inset:0;background:radial-gradient(ellipse 80px 90px at 118px 110px,#b8866a,rgba(184,134,106,0) 75%),linear-gradient(180deg,#2e2e2e 0%,#4a4a4a 45%,#a8a8a8 75%,#c8c8c8 100%)"></div><div class="pro-label">Lucas Renner</div></div>

<!-- TESTIMONIALS -->
<div class="testi-bg"></div>
<h2 class="head abs" style="left:0;top:3470px;width:1200px;text-align:center;font-size:39px">Our Clients Testimonials</h2>
<div class="mark abs" style="left:593px;top:3534px"></div>
<div class="av" role="img" aria-label="Client portrait" style="left:262px;top:3552px;width:50px;height:50px;background:radial-gradient(circle at 50% 45%,#d2b09a,#6e7c8c 70%)"></div>
<div class="av" role="img" aria-label="Client portrait" style="left:378px;top:3632px;width:54px;height:54px;background:radial-gradient(circle at 50% 45%,#e2c0a0,#a07a58 70%)"></div>
<div class="av" role="img" aria-label="Client portrait" style="left:556px;top:3600px;width:86px;height:86px;background:radial-gradient(circle at 50% 45%,#c89a7c,#6c6c70 70%)"></div>
<div class="av" role="img" aria-label="Client portrait" style="left:830px;top:3618px;width:50px;height:50px;background:radial-gradient(circle at 50% 45%,#d4ac90,#5a6a80 70%)"></div>
<div class="av" role="img" aria-label="Client portrait" style="left:1044px;top:3566px;width:56px;height:56px;background:radial-gradient(circle at 50% 45%,#b88a70,#2e2420 70%)"></div>
<div class="av" role="img" aria-label="Client portrait" style="left:132px;top:3722px;width:56px;height:56px;background:radial-gradient(circle at 50% 45%,#a87a5c,#3e4a5c 70%)"></div>
<div class="av" role="img" aria-label="Client portrait" style="left:1028px;top:3722px;width:54px;height:54px;background:radial-gradient(circle at 50% 45%,#d8a888,#8a5e40 70%)"></div>
<p class="abs" style="left:210px;top:3702px;width:780px;text-align:center;font-style:italic;font-size:16px;line-height:26.5px;color:#555">“Lorem ipsum dolor sit amet, consectetur adipiscing elit, sed do eiusmod tempor incididunt ut labore et dolore magna aliqua. Quis ipsum suspendisse ultrices gravida. Risus commodo viverra maecenas accumsan lacus vel facilisis.Lorem ipsum dolor sit amet, consectetur adipiscing elit, sed do eiusmod tempor incididunt ut labore et dolore magna aliqua”</p>
<div class="abs" style="left:0;top:3820px;width:1200px;text-align:center;font-family:Heebo,sans-serif;font-weight:500;font-size:20px;color:var(--ink)">- Graham Ellison</div>
<div class="abs" style="left:0;top:3850px;width:1200px;text-align:center;color:var(--gold);font-size:15px;letter-spacing:1px">★★★★★</div>
<div class="abs" style="left:540px;top:3890px;width:28px;height:3px;background:#b5b9bf"></div>
<div class="abs" style="left:576px;top:3889px;width:46px;height:4px;background:var(--ink)"></div>
<div class="abs" style="left:630px;top:3890px;width:28px;height:3px;background:#b5b9bf"></div>

<!-- BLOGS -->
<h2 class="head abs" style="left:0;top:4050px;width:1200px;text-align:center;font-size:39px">Our Latest Blogs</h2>
<div class="mark abs" style="left:593px;top:4114px"></div>
<div class="arrow-circle outline" style="left:48px;top:4371px"><svg width="10" height="14" viewBox="0 0 10 14"><path d="M8 1L2 7l6 6" stroke="#222" stroke-width="2" fill="none"/></svg></div>
<div class="arrow-circle filled" style="left:1110px;top:4371px"><svg width="10" height="14" viewBox="0 0 10 14"><path d="M2 1l6 6-6 6" stroke="#fff" stroke-width="2" fill="none"/></svg></div>
<article class="blog-card" style="left:112px"><div class="photo" role="img" aria-label="Team of lawyers reviewing files at a laptop" style="left:0;top:0;width:300px;height:192px;background:radial-gradient(ellipse 120px 70px at 150px 140px,#e8ecf0,rgba(232,236,240,0) 75%),linear-gradient(170deg,#d6dbe0 0%,#8c98a6 40%,#2e3a4e 80%,#1e2838 100%)"></div><h3>Lorem ipsum dolor sit amet</h3><p>Lorem ipsum dolor sit amet, consetur adipiscing elit, sed do sod tempoidint ut labore et dolore magna aliquaQuis psum isse ultrices gravida.</p><svg class="go" width="14" height="12" viewBox="0 0 14 12"><path d="M0 6h11M7 1l5 5-5 5" stroke="#b8813e" stroke-width="2.2" fill="none"/></svg></article>
<article class="blog-card" style="left:450px"><div class="photo" role="img" aria-label="Attorney standing in a modern office" style="left:0;top:0;width:300px;height:192px;background:radial-gradient(ellipse 60px 90px at 150px 110px,#eeeae4,rgba(238,234,228,0) 75%),linear-gradient(90deg,#4a3424 0%,#8a6444 30%,#c8b49c 55%,#6a4c34 100%)"></div><h3>Lorem ipsum dolor sit amet</h3><p>Lorem ipsum dolor sit amet, consetur adipiscing elit, sed do sod tempoidint ut labore et dolore magna aliquaQuis psum isse ultrices gravida.</p><svg class="go" width="14" height="12" viewBox="0 0 14 12"><path d="M0 6h11M7 1l5 5-5 5" stroke="#b8813e" stroke-width="2.2" fill="none"/></svg></article>
<article class="blog-card" style="left:788px"><div class="photo" role="img" aria-label="Lawyers on the steps of a columned courthouse" style="left:0;top:0;width:300px;height:192px;background:radial-gradient(ellipse 90px 60px at 220px 80px,#3a3a3e,rgba(58,58,62,0) 75%),linear-gradient(180deg,#f2f0ec 0%,#d6d2cc 40%,#a8a49c 70%,#7c7870 100%)"></div><h3>Lorem ipsum dolor sit amet</h3><p>Lorem ipsum dolor sit amet, consetur adipiscing elit, sed do sod tempoidint ut labore et dolore magna aliquaQuis psum isse ultrices gravida.</p><svg class="go" width="14" height="12" viewBox="0 0 14 12"><path d="M0 6h11M7 1l5 5-5 5" stroke="#b8813e" stroke-width="2.2" fill="none"/></svg></article>

<!-- FOOTER -->
<footer class="footer"></footer>
<div class="abs" style="left:110px;top:4840px;color:#fff;font-family:Heebo,sans-serif;font-weight:700;font-size:30px;line-height:34px;text-transform:uppercase">Haverlock<br>Trial Firm</div>
<div class="f-head" style="left:392px;top:4780px">Quick Links</div>
<ul class="f-links">
  <li>Home</li><li>About Us</li><li>Practice Area</li><li>Professionals</li><li>Resources &amp; Advisories</li><li>Blog</li><li>Contact Us</li>
</ul>
<div class="f-head" style="left:636px;top:4776px">Contact Us</div>
<div class="f-item" style="left:636px;top:4822px"><div class="ic-gold"><svg width="18" height="18" viewBox="0 0 24 24"><path fill="#fff" d="M6.6 10.8a15 15 0 0 0 6.6 6.6l2.2-2.2c.3-.3.7-.4 1-.2 1.1.4 2.3.6 3.6.6.6 0 1 .4 1 1V20c0 .6-.4 1-1 1A17 17 0 0 1 3 4c0-.6.4-1 1-1h3.5c.6 0 1 .4 1 1 0 1.3.2 2.5.6 3.6.1.3 0 .7-.2 1z"/></svg></div><div><b>PHONE NO:</b><br>+1(888) 888 8888</div></div>
<div class="f-item" style="left:636px;top:4890px"><div class="ic-gold"><svg width="18" height="18" viewBox="0 0 24 24"><path fill="#fff" d="M3 5h18v14H3z"/><path fill="none" stroke="#b8813e" stroke-width="2" d="M3 6l9 7 9-7"/></svg></div><div><b>EMAIL:</b><br>haverlocktrialfirm.com</div></div>
<div class="f-item" style="left:636px;top:4956px"><div class="ic-gold"><svg width="16" height="20" viewBox="0 0 16 20"><path fill="#fff" d="M8 0a8 8 0 0 0-8 8c0 6 8 12 8 12s8-6 8-12a8 8 0 0 0-8-8zm0 11a3 3 0 1 1 0-6 3 3 0 0 1 0 6z"/></svg></div><div><b>LOCATION:</b><br>Lorem ipsum dolor sit amet<br>consetur adipiscing.USA</div></div>
<div class="f-head" style="left:908px;top:4776px">Social Media</div>
<div class="social on" role="img" aria-label="Social profile link" style="left:914px;top:4822px"></div>
<div class="social" role="img" aria-label="Social profile link" style="left:977px;top:4822px"></div>
<div class="social" role="img" aria-label="Social profile link" style="left:1036px;top:4822px"></div>
<div class="abs" style="left:112px;top:5040px;width:976px;height:1px;background:#3a4a60"></div>
<div class="abs" style="left:0;top:5062px;width:1200px;text-align:center;color:#fff;font-size:14px">Copyright © 2025 Haverlock Trial Firm PLLC | All Rights Reserved</div>

</body>
</html>
```